International oil and gas consultancy needs a business card design

We need a business card design for a new oil and gas consultancy business based in Perth Australia. This is a professional services business and needs a moderately conservative type of business card. The business card also needs to be simple and uncluttered. The colour of the business logo is dark red (see attached file).
The front of the card should have a white background and mainly black lettering and perhaps some use of dark red and/or grey (your choice).
The back of the card should have a light grey background with dark red, black and or both dark red & black lettering (your choice).
Please find attached a clear brief of how I would like the business card designed.
Updates

Hello Everyone, I have slightly modified the brief. The main change is to incorporate some dark red and grey colours into the card, while still keeping the black lettering dominant. I have made the changes in the attached detailed brief document. Regards

Please note, the front of the card must say Harbour Ledger Services (in addition to the logo).

Industry/Entity Type

Conservative

Requirements
Must have
• brief has been updated. please refer to attachment for details.

Front of the card MUST say Harbour Ledger Services (in addition to the logo)

```html
<!DOCTYPE html>
<html lang="en">
<head>
<meta charset="utf-8">
<title>Harbour Ledger Services – Business Card</title>
<link rel="stylesheet" href="https://fonts.googleapis.com/css2?family=Oswald:wght@400;600&family=Open+Sans:wght@400;600&display=swap">
<style>
  :root {
    --page: #ecebe8;
    --card: #ffffff;
    --card-shade: #f1f1f1;
    --red: #9e1b22;
    --ink: #2b2b2b;
    --grey: #8a8a8a;
    --rule: #9a9a9a;
    --band-text: #ffffff;
  }
  * { box-sizing: border-box; margin: 0; padding: 0; }
  html, body { width: 1057px; height: 1200px; overflow: hidden; }
  body {
    background: var(--page);
    font-family: "Open Sans", Arial, sans-serif;
    color: var(--ink);
    display: flex;
    flex-direction: column;
    align-items: center;
    justify-content: center;
    gap: 80px;
  }
  .card {
    position: relative;
    width: 860px;
    height: 490px;
    background: radial-gradient(ellipse at 45% 45%, var(--card) 40%, var(--card-shade) 100%);
    box-shadow: 0 6px 18px rgba(0,0,0,0.18);
    overflow: hidden;
  }
  .band {
    position: absolute;
    left: 0; right: 0; bottom: 48px;
    height: 46px;
    background: var(--red);
    color: var(--band-text);
    font-size: 17px;
    letter-spacing: 4px;
    display: flex;
    align-items: center;
    padding-left: 300px;
  }
  .wordmark {
    font-family: "Oswald", Arial, sans-serif;
    font-weight: 600;
    color: var(--red);
    text-transform: uppercase;
    letter-spacing: 2px;
    line-height: 1.05;
  }
  /* front */
  .card--front .wordmark {
    position: absolute;
    left: 0; right: 0; top: 150px;
    text-align: center;
    font-size: 52px;
  }
  .card--front .band { padding-left: 0; justify-content: center; }
  /* back */
  .card--back .wordmark {
    position: absolute;
    left: 60px; top: 170px;
    width: 260px;
    font-size: 34px;
  }
  .identity {
    position: absolute;
    left: 380px; top: 46px;
  }
  .identity__name {
    font-family: "Oswald", Arial, sans-serif;
    font-size: 46px;
    font-weight: 400;
    letter-spacing: 2px;
    text-transform: uppercase;
  }
  .identity__title {
    font-family: "Oswald", Arial, sans-serif;
    font-size: 18px;
    letter-spacing: 3px;
    color: var(--grey);
    text-transform: uppercase;
  }
  .rule {
    position: absolute;
    height: 5px;
    background: var(--rule);
  }
  .rule--top { left: 250px; top: 150px; width: 110px; }
  .rule--mid { left: 380px; top: 150px; width: 420px; height: 3px; }
  .rule--side { left: 360px; top: 150px; width: 3px; height: 200px; }
  .contacts {
    position: absolute;
    left: 400px; top: 180px;
    list-style: none;
    font-size: 16px;
    color: var(--grey);
  }
  .contacts li { display: flex; align-items: center; gap: 14px; margin-bottom: 14px; }
  .contacts svg { width: 26px; height: 26px; flex: none; }
</style>
</head>
<body>

<section class="card card--front" aria-label="Card front">
  <div class="wordmark">Harbour Ledger Services</div>
  <div class="band">www.harbourledger.com</div>
</section>

<section class="card card--back" aria-label="Card back">
  <div class="wordmark">Harbour Ledger Services</div>

  <div class="identity">
    <div class="identity__name">Marcus Reid</div>
    <div class="identity__title">General Manager</div>
  </div>

  <div class="rule rule--top"></div>
  <div class="rule rule--mid"></div>
  <div class="rule rule--side"></div>

  <ul class="contacts">
    <li>
      <svg viewBox="0 0 26 26" aria-hidden="true"><rect width="26" height="26" fill="#8a8a8a"/><path d="M8 6l3 0 1 4-2 1c1 2 3 4 5 5l1-2 4 1 0 3c-7 0-12-5-12-12z" fill="#fff"/></svg>
      08 9321 4470
    </li>
    <li>
      <svg viewBox="0 0 26 26" aria-hidden="true"><rect width="26" height="26" fill="#8a8a8a"/><rect x="9" y="5" width="8" height="16" rx="1.5" fill="#fff"/><rect x="10.5" y="7" width="5" height="10" fill="#8a8a8a"/></svg>
      08 9321 4471
    </li>
    <li>
      <svg viewBox="0 0 26 26" aria-hidden="true"><rect width="26" height="26" fill="#8a8a8a"/><rect x="5" y="8" width="16" height="11" fill="#fff"/><path d="M5 8l8 6 8-6" fill="none" stroke="#8a8a8a" stroke-width="1.5"/></svg>
      m.reid@harbourledger.com
    </li>
    <li>
      <svg viewBox="0 0 26 26" aria-hidden="true"><rect width="26" height="26" fill="#8a8a8a"/><circle cx="13" cy="13" r="7" fill="none" stroke="#fff" stroke-width="1.6"/><path d="M6 13h14M13 6c-3 4-3 10 0 14M13 6c3 4 3 10 0 14" fill="none" stroke="#fff" stroke-width="1.2"/></svg>
      www.harbourledger.com
    </li>
  </ul>

  <div class="band">24 Quay Road, Level 3, Perth WA</div>
</section>

</body>
</html>
```